Brisk Coatings business card for residential and commercial painting

A clean, professional design. Easy to read
Eye catching and elegant
Front could have some color variations
On the back of card I would like all black with signature logo

*Attached is my current business card and the items I want displayed

Contact Information for Business Card

Email, phone number, website, and owner name

Font styles to use
Serif

Requirements
Must have
• My logo with cool design and perhaps some paint splatter

```html
<!DOCTYPE html>
<html lang="en">
<head>
<meta charset="utf-8">
<title>Brisk Coatings – Business Card</title>
<link href="https://fonts.googleapis.com/css2?family=Roboto:ital,wght@0,400;0,700;1,700&display=swap" rel="stylesheet">
<style>
  :root {
    --backdrop: #3a3a3a;
    --card: #1e1e1f;
    --ink-white: #ffffff;
    --accent-blue: #1a8fe3;
    --emboss-grey: #6d6e70;
    --muted: #d9d9d9;
  }
  * { margin: 0; padding: 0; box-sizing: border-box; }
  html, body { width: 799px; height: 1200px; overflow: hidden; }
  body {
    background: var(--backdrop);
    font-family: "Roboto", Arial, sans-serif;
    position: relative;
  }
  .card {
    position: absolute;
    left: 80px;
    width: 640px;
    height: 366px;
    background: var(--card);
    border-radius: 3px;
    box-shadow: 0 10px 24px rgba(0,0,0,0.45);
    overflow: hidden;
  }
  .card--front { top: 130px; }
  .card--back { top: 704px; }

  /* Front */
  .brand-lockup {
    position: absolute;
    left: 0; right: 0; top: 128px;
    display: flex; flex-direction: column; align-items: center;
  }
  .brand-name {
    display: flex; align-items: center; gap: 14px;
    color: var(--ink-white);
    font-weight: 700;
    font-size: 50px;
    letter-spacing: 1px;
    text-transform: uppercase;
    line-height: 1;
  }
  .brand-square {
    width: 22px; height: 22px;
    background: var(--accent-blue);
  }
  .brand-web {
    margin-top: 14px;
    margin-left: 150px;
    font-size: 17px;
    letter-spacing: 1px;
    color: var(--ink-white);
  }
  .brand-web .domain { color: var(--accent-blue); }

  /* Back */
  .owner {
    position: absolute; left: 40px; top: 38px;
  }
  .owner-name {
    color: var(--accent-blue);
    font-weight: 700; font-style: italic;
    font-size: 22px;
  }
  .owner-role {
    color: var(--ink-white);
    font-size: 15px;
    margin-top: 4px;
  }
  .emboss-name {
    position: absolute; left: 0; right: 0; top: 150px;
    text-align: center;
    color: var(--emboss-grey);
    font-weight: 700;
    font-size: 48px;
    letter-spacing: 1px;
    text-transform: uppercase;
  }
  .contact-row {
    position: absolute; left: 40px; right: 40px; bottom: 40px;
    display: flex; justify-content: space-between; align-items: center;
    list-style: none;
  }
  .contact-item {
    display: flex; align-items: center; gap: 8px;
    color: var(--ink-white);
    font-size: 15px;
  }
  .contact-icon { width: 16px; height: 16px; fill: var(--accent-blue); }
</style>
</head>
<body>

<section class="card card--front" aria-label="Card front">
  <div class="brand-lockup">
    <div class="brand-name"><span class="brand-square"></span>Brisk Coatings</div>
    <div class="brand-web">www.<span class="domain">briskcoatingstn</span>.com</div>
  </div>
</section>

<section class="card card--back" aria-label="Card back">
  <div class="owner">
    <div class="owner-name">Marco "MJ"</div>
    <div class="owner-role">Owner - Licensed &amp; Insured</div>
  </div>

  <div class="emboss-name">Brisk Coatings</div>

  <ul class="contact-row">
    <li class="contact-item">
      <svg class="contact-icon" viewBox="0 0 16 16" aria-hidden="true">
        <path d="M2 5c0-2 2-3 6-3s6 1 6 3v1h-3V4.5H5V6H2z"/>
        <rect x="3" y="7" width="10" height="7" rx="1"/>
      </svg>
      931-555-0148
    </li>
    <li class="contact-item">
      <svg class="contact-icon" viewBox="0 0 16 16" aria-hidden="true">
        <path d="M1 3h14v10H1z M2 4l6 5 6-5" fill="var(--accent-blue)"/>
        <path d="M2 4l6 5 6-5" fill="none" stroke="var(--card)" stroke-width="1.2"/>
      </svg>
      hello@briskcoatingstn.com
    </li>
    <li class="contact-item">
      <svg class="contact-icon" viewBox="0 0 16 16" aria-hidden="true">
        <circle cx="8" cy="8" r="7"/>
        <path d="M1 8h14M8 1c-3 3-3 11 0 14M8 1c3 3 3 11 0 14" fill="none" stroke="var(--card)" stroke-width="1"/>
      </svg>
      briskcoatingstn.com
    </li>
  </ul>
</section>

</body>
</html>
```